Box for a Bold Bathroom - stylish minimalist package for a modern upscale brand

We need an adaptable package design using a color label on a brown box, or just a brown box with 2 or 3 color printing. The best design would be one that is adaptable for either use.

Our first products launching under this brand will be a series of medicine cabinets and mirrors, and our cartons can vary in size from 500x100x600 mm to 1200x300x1000 mm

About us: we produce a variety of bathroom fixtures including medicine cabinets, mirrors, vanities, etc. You've likely seen our products - we do manufacturing for Brantley, Marlowe, Thistle Cove, Dunmore & Pike, and others.

A version of our logo is attached for reference; we use it in a variety of color mixes depending on application. Vector available if needed or can be used FPO and our team will replace.

These are our colors, please take note and ignore the 'color' field:

Light Blue: C:66%/M:6%/Y:22%/K:0%; H:189° S:65% B:78%
Light Grey: C:35%/M:26%/Y:24%/K:0%; H:213° S:5% B:70%
Dark Blue: C:90%/M:50%/Y:44%/K:20%; H:189° S:82% B:43%
Dark Grey: C:70%/M:60%/Y:54%/K:38%; H:213° S:11% B:30%

Reason: Some revisions still outstanding before we can make selection, and some submissions we have agreed to wait for. Please submit all work ASAP so our team can provide feedback to you. Thanks!

Target Market(s)

DIY'ers; home renovators

Industry/Entity Type

Home Improvement

Font styles to use
Sans Serif

Requirements
Must have
• 1. Brand logo w/ logotype
• 2. Brand name without logo (can be on shipping mark side)
• 3. Multi-lingual En/Fr/Es (you do not need to include multi-lingual content but must allow space for our own translations if you do not)
• 4. Shipping/Handling Glyphs on 5 sides (all but bottom)
• i.e. fragile, this way up, team lift or mech lift, clamp or no clamp, max-stack
• 5. Two sides should include a marked 4" x 4" area for affixing labels (e.g. UPC, SSCC, etc.) ideally with a dotted line or corner marks or similar.
• 6. Shipping mark details or space for them (should be on the smallest side, only needed on one but can be on both) [see example file of shipping mark informations]
Nice to have
• Design that can be used either with color label on brown box, or brown box only.
• If designing for color label; please see the sample images included. Lifestyle should be prominent, the inside photo being smaller to help show interior features. These photos are obviously not useful for brown-box design.

```html
<!DOCTYPE html>
<html lang="en">
<head>
<meta charset="utf-8">
<title>Clearhaven – Mailer Carton Dieline</title>
<link rel="stylesheet" href="https://fonts.googleapis.com/css2?family=Jost:wght@400;500&family=Oswald:wght@400&display=swap">
<style>
  :root {
    --kraft: #b38f72;
    --kraft-light: #b8967a;
    --cut-line: #6e5a4a;
    --dark-blue: #2d6570;
    --dark-grey: #434a52;
    --light-blue: #4fb8c8;
    --label-white: #fbfbfb;
    --bg-centre: #f2f3f4;
    --bg-edge: #e3e5e7;
  }
  html, body {
    margin: 0;
    width: 1200px;
    height: 1200px;
    overflow: hidden;
    background: radial-gradient(circle at 50% 50%, var(--bg-centre) 0%, var(--bg-edge) 75%);
  }
  .dieline { display: block; width: 1200px; height: 1200px; }
  .panel { fill: var(--kraft); stroke: var(--cut-line); stroke-width: 0.8; }
  .flap { fill: var(--kraft-light); stroke: var(--cut-line); stroke-width: 0.8; }
  .band { fill: var(--dark-blue); }
  .slot { fill: #ffffff; stroke: var(--cut-line); stroke-width: 0.6; }
  .brand-name {
    font-family: "Jost", sans-serif;
    font-weight: 500;
    fill: var(--dark-grey);
    letter-spacing: 1.6px;
  }
  .brand-dot { fill: var(--light-blue); }
  .glyph-frame { fill: none; stroke: var(--dark-grey); stroke-width: 1.2; }
  .glyph-ink { fill: var(--dark-grey); }
  .glyph-line { fill: none; stroke: var(--dark-grey); stroke-width: 1.6; }
  .glyph-num { font-family: "Oswald", sans-serif; font-size: 13px; fill: var(--dark-grey); }
  .ship-mark { font-family: "Oswald", sans-serif; font-size: 6.4px; fill: var(--dark-grey); letter-spacing: 0.3px; }
  .field-label { font-family: "Oswald", sans-serif; font-size: 9px; fill: var(--dark-grey); letter-spacing: 0.4px; }
  .label-area { fill: var(--label-white); stroke: #9a9a9a; stroke-width: 0.5; }
  .label-text { font-family: "Oswald", sans-serif; font-size: 3.4px; fill: #555; }
  .label-rule { stroke: #777; stroke-width: 0.6; }
</style>
</head>
<body>
<svg class="dieline" viewBox="0 0 1200 1200" xmlns="http://www.w3.org/2000/svg" aria-label="Clearhaven mailer carton dieline">
  <defs>
    <symbol id="glyph-this-way-up" viewBox="0 0 24 24">
      <rect class="glyph-frame" x="0.6" y="0.6" width="22.8" height="22.8"/>
      <path class="glyph-ink" d="M8 4 L11.5 9 H9.2 V17 H6.8 V9 H4.5 Z M16 4 L19.5 9 H17.2 V17 H14.8 V9 H12.5 Z"/>
      <rect class="glyph-ink" x="4" y="19" width="16" height="2"/>
    </symbol>
    <symbol id="glyph-handle-care" viewBox="0 0 24 24">
      <rect class="glyph-frame" x="0.6" y="0.6" width="22.8" height="22.8"/>
      <path class="glyph-line" d="M3 8 L7 4 L10 8 L8 12 M21 8 L17 4 L14 8 L16 12"/>
      <rect class="glyph-ink" x="8" y="12" width="8" height="7" rx="1"/>
    </symbol>
    <symbol id="glyph-fragile" viewBox="0 0 24 24">
      <rect class="glyph-frame" x="0.6" y="0.6" width="22.8" height="22.8"/>
      <path class="glyph-ink" d="M7 3 H17 L16 10 Q15 13 13 13.5 V18 H16 V20 H8 V18 H11 V13.5 Q9 13 8 10 Z"/>
    </symbol>
    <symbol id="glyph-no-clamp" viewBox="0 0 24 24">
      <rect class="glyph-frame" x="0.6" y="0.6" width="22.8" height="22.8"/>
      <rect class="glyph-line" x="7" y="7" width="10" height="10"/>
      <path class="glyph-line" d="M7 7 L17 17 M17 7 L7 17"/>
      <path class="glyph-ink" d="M2 11 H5 V13 H2 Z M19 11 H22 V13 H19 Z"/>
    </symbol>
    <symbol id="glyph-stack-limit" viewBox="0 0 24 24">
      <rect class="glyph-frame" x="0.6" y="0.6" width="22.8" height="22.8"/>
      <text class="glyph-num" x="12" y="17" text-anchor="middle">10</text>
      <rect class="glyph-ink" x="4" y="19" width="16" height="1.6"/>
    </symbol>
    <g id="glyph-row">
      <use href="#glyph-this-way-up" x="0" y="0" width="24" height="24"/>
      <use href="#glyph-handle-care" x="27" y="0" width="24" height="24"/>
      <use href="#glyph-fragile" x="54" y="0" width="24" height="24"/>
      <use href="#glyph-no-clamp" x="81" y="0" width="24" height="24"/>
      <use href="#glyph-stack-limit" x="108" y="0" width="24" height="24"/>
    </g>
    <g id="label-sticker">
      <rect class="label-area" x="0" y="0" width="29" height="28"/>
      <line class="label-rule" x1="10" y1="3" x2="27" y2="3"/>
      <text class="label-text" x="2" y="9">SSCC</text>
      <text class="label-text" x="2" y="14">LABEL</text>
      <line class="label-rule" x1="2" y1="18" x2="27" y2="18"/>
      <line class="label-rule" x1="2" y1="22" x2="20" y2="22"/>
    </g>
  </defs>

  <!-- lid closure flap and ears -->
  <rect class="flap" x="441" y="124" width="317" height="132"/>
  <path class="flap" d="M441,124 L441,256 L340,256 Q326,256 326,242 L326,220 C326,160 380,124 436,124 Z"/>
  <path class="flap" d="M758,124 L758,256 L860,256 Q874,256 874,242 L874,220 C874,160 820,124 764,124 Z"/>

  <!-- lid panel and dust flaps -->
  <path class="flap" d="M441,256 L346,280 Q326,286 326,304 L326,488 Q326,506 346,512 L441,532 Z"/>
  <path class="flap" d="M758,256 L854,280 Q874,286 874,304 L874,488 Q874,506 854,512 L758,532 Z"/>
  <rect class="panel" x="441" y="256" width="317" height="276"/>
  <rect class="band" x="441" y="256" width="317" height="5.5"/>
  <rect class="band" x="441" y="528" width="317" height="5.5"/>

  <g class="brand-lockup">
    <circle class="brand-dot" cx="600" cy="380" r="12"/>
    <text class="brand-name" x="600" y="418" font-size="12.5" text-anchor="middle">CLEARHAVEN</text>
  </g>
  <use href="#glyph-row" x="532" y="496"/>

  <!-- back wall -->
  <path class="flap" d="M441,535 L316,538 L316,662 L441,665 Z"/>
  <path class="flap" d="M758,535 L884,538 L884,662 L758,665 Z"/>
  <rect class="panel" x="441" y="534" width="317" height="131"/>

  <!-- base with side walls and locking flaps -->
  <path class="panel" d="M310,665 L179,665 L179,738 Q172,740 172,748 L172,866 Q172,874 179,876 L179,944 L310,944 Z"/>
  <path class="panel" d="M890,665 L1021,665 L1021,738 Q1028,740 1028,748 L1028,866 Q1028,874 1021,876 L1021,944 L890,944 Z"/>
  <rect class="panel" x="310" y="665" width="131" height="279"/>
  <rect class="panel" x="758" y="665" width="132" height="279"/>
  <rect class="panel" x="441" y="665" width="317" height="279"/>
  <rect class="band" x="310" y="665" width="580" height="5.5"/>
  <rect class="band" x="310" y="938.5" width="580" height="5.5"/>
  <rect class="slot" x="438" y="734" width="6" height="140" rx="3"/>
  <rect class="slot" x="755" y="734" width="6" height="140" rx="3"/>

  <!-- base panel branding, upside down -->
  <g transform="rotate(180 600 800)">
    <use href="#glyph-row" x="532" y="896"/>
    <text class="brand-name" x="600" y="818" font-size="12.5" text-anchor="middle">CLEARHAVEN</text>
    <circle class="brand-dot" cx="600" cy="778" r="12"/>
  </g>

  <!-- left side wall -->
  <g transform="translate(432 680) rotate(90)">
    <use href="#glyph-row" x="0" y="0"/>
  </g>
  <g transform="translate(424 930) rotate(-90)">
    <text class="field-label" x="0" y="0">COLOR :</text>
    <text class="field-label" x="0" y="-12">MODEL :</text>
  </g>
  <use href="#label-sticker" x="321" y="902"/>

  <!-- right side wall: shipping mark -->
  <g transform="translate(860 690) rotate(90)">
    <text class="brand-name" x="0" y="0" font-size="10.5">CLEARHAVEN</text>
  </g>
  <rect x="776" y="690" width="75" height="3" fill="var(--dark-grey)"/>
  <g transform="translate(845 698) rotate(90)" class="ship-mark">
    <text x="0" y="0">LOT #: 120456</text>
    <text x="0" y="8">ITEM #: CH-2040</text>
    <text x="0" y="16">DIM: 100 X 45 X 15 CM</text>
    <text x="0" y="24">NW/GW: 18 / 21 KG</text>
    <text x="0" y="32">CUBE: 0.07 M3</text>
    <text x="0" y="40">QTY: 1</text>
    <text x="0" y="48">CASE: 1 OF 1</text>
  </g>
  <g transform="translate(768 930) rotate(-90)">
    <use href="#glyph-row" x="0" y="0" width="132"/>
  </g>
  <use href="#label-sticker" x="852" y="902"/>

  <!-- front wall -->
  <path class="flap" d="M441,946 L316,948 L316,1072 L441,1074 Z"/>
  <path class="flap" d="M758,946 L884,948 L884,1072 L758,1074 Z"/>
  <rect class="panel" x="441" y="944" width="317" height="130"/>
  <g transform="rotate(180 515 972)">
    <use href="#glyph-row" x="462" y="962" transform="translate(462 962) scale(0.8) translate(-462 -962)"/>
  </g>
  <g transform="rotate(180 680 1048)">
    <text class="brand-name" x="618" y="1052" font-size="9.5">CLEARHAVEN</text>
    <circle class="brand-dot" cx="608" cy="1048" r="6"/>
  </g>
</svg>
</body>
</html>
```